Global (re)insurance broker needs a business card design

We need a classic business card for our company that is headquartered in SG, with offices in Malaysia and Dubai. We specialise in insurance and reinsurance broking and consultancy for our global clients.

```html
<!DOCTYPE html>
<html lang="en">
<head>
<meta charset="utf-8">
<title>Korvale Business Card</title>
<link rel="stylesheet" href="https://fonts.googleapis.com/css2?family=Open+Sans:wght@400;700;800&display=swap">
<style>
  :root {
    --page: #2b2b2e;
    --card: #161616;
    --blue: #2a4b9f;
    --green: #c4dbb6;
    --white: #f2f2f2;
  }
  * { margin: 0; padding: 0; box-sizing: border-box; }
  html, body { width: 1200px; height: 947px; overflow: hidden; }
  body {
    background: var(--page);
    font-family: "Open Sans", Arial, sans-serif;
    position: relative;
  }
  .card {
    position: absolute;
    left: 250px;
    width: 700px;
    height: 400px;
    background: var(--card);
    border: 2px solid var(--blue);
    border-radius: 26px;
    overflow: hidden;
  }
  .card--front { top: 49px; }
  .card--back { top: 498px; }

  .wordmark {
    font-weight: 800;
    color: var(--green);
    letter-spacing: 4px;
    line-height: 1;
  }
  .card--front .wordmark {
    position: absolute;
    left: 0; right: 0; top: 50%;
    transform: translateY(-50%);
    text-align: center;
    font-size: 112px;
  }
  .card--back .wordmark {
    position: absolute;
    left: 56px;
    top: 168px;
    font-size: 56px;
    letter-spacing: 2px;
  }

  .divider {
    position: absolute;
    left: 372px;
    top: 60px;
    width: 1.5px;
    height: 236px;
    background: var(--green);
  }

  .contact {
    position: absolute;
    left: 400px;
    top: 58px;
    color: var(--white);
    font-size: 15px;
    line-height: 1.45;
  }
  .contact__name {
    font-size: 25px;
    font-weight: 800;
    line-height: 1.1;
  }
  .contact__first { color: var(--blue); }
  .contact__last { color: var(--green); }
  .contact__role { font-size: 16px; margin-bottom: 14px; }
  .contact__row { display: flex; align-items: center; gap: 8px; }
  .contact__row svg { width: 12px; height: 12px; flex: none; fill: var(--white); }
  .contact__address { margin-top: 14px; }

  .edge-band {
    position: absolute;
    left: 0; bottom: 0;
    width: 700px;
    height: 80px;
  }
</style>
</head>
<body>

<section class="card card--front">
  <div class="wordmark">KORVALE</div>
</section>

<section class="card card--back">
  <div class="wordmark">KORVALE</div>
  <div class="divider"></div>

  <div class="contact">
    <p class="contact__name"><span class="contact__first">Lena</span> <span class="contact__last">Hart</span></p>
    <p class="contact__role">Chief Operating Officer</p>
    <p class="contact__row">
      <svg viewBox="0 0 24 24" aria-hidden="true"><path d="M6.6 10.8a15.1 15.1 0 0 0 6.6 6.6l2.2-2.2a1 1 0 0 1 1-.25 11.4 11.4 0 0 0 3.6.6 1 1 0 0 1 1 1V20a1 1 0 0 1-1 1A17 17 0 0 1 3 4a1 1 0 0 1 1-1h3.5a1 1 0 0 1 1 1c0 1.25.2 2.45.6 3.6a1 1 0 0 1-.25 1z"/></svg>
      +65 9000 4182
    </p>
    <p class="contact__row">
      <svg viewBox="0 0 24 24" aria-hidden="true"><path d="M2 5h20v14H2zM4 7v.5l8 5 8-5V7z"/></svg>
      lena@korvale.com
    </p>
    <p class="contact__row">
      <svg viewBox="0 0 24 24" aria-hidden="true"><circle cx="12" cy="12" r="10"/></svg>
      www.korvale.com
    </p>
    <p class="contact__address">22 Harbour Lane,<br>Meridian Tower #08-04,<br>Singapore 010203</p>
  </div>

  <svg class="edge-band" viewBox="0 0 700 80" aria-hidden="true">
    <polygon points="0,58 560,58 566,54 0,54" fill="#2a4b9f"/>
    <polygon points="0,64 572,64 584,24 700,24 700,80 0,80" fill="#c4dbb6"/>
  </svg>
</section>

</body>
</html>
```